Online Dating Website called WinkAtWheel.com

PLEASE CAN ALL PARTICIPATING DESIGNERS PLEASE SUBMIT ALL PAGES AS DETAILED IN THE ORIGINAL BRIEF BELOW WITHIN 48 HOURS TO AVOID WINKATWHEEL EXTENDING THE CONTEST FURTHER.

We have an online dating website that is 95% fully functional and now require an exciting and creative designer to help us create the best dating experience. We are looking for your ideas on a couple of our key pages. These are our landing, profile and search page. We already have a homepage that we are happy with and winning designers will look to build upon the foundations of the homepage and extend them through their designs.

The premise of the site is the idea that if you've ever seen someone out driving and wished you could communicate because you found them attractive, how would you? Well with WinkAtWheel.com you can. Just enter their vehicle registration number (license plate) in to the website in order to get in touch, flirt and develop a relationship. It also allows users to find each other based on other criteria. It acts as both a specialist service and a normal dating website.

The pages that require developing are 1) our landing page, this is the page users see when they first login to the site, it comprises various pieces of information but it's primary function is a live feed of events generated based on the users favourited profiles and interactions with the user. 2) The profile page is the page where users can edit their own information, given the nature of this page we are looking for a creative design that gives this page some flair. 3) Finally we are looking for ideas for our search page, this page needs to provide a list of users who meet the user's search requirements and display the profile of a selected user.
Updates

Project Deadline Extended
Reason: We've asked for certain pages in our brief to be designed and this still hasn't been done. We've contacted the designers that have currently submitted designs and requested this several times. We still await for this to happen.

Target Market(s)

Male or Female age 18+

Industry/Entity Type

Dating

Requirements
Must have
• Our must have feature is a designer with an open mind. The functionality of the site must be present, all we ask is for you to be creative with the layout. Think out side of the box, change the colours, the layout, and the background as you feel. Make it look current and appealing to the user.
Nice to have
• Theme's carried through from the home page
Should not have
• Do not include Comic Sans or Times New Roman font in your designs.

```html
<!DOCTYPE html>
<html lang="en">
<head>
<meta charset="utf-8">
<title>WinkAtWheel – My Profile</title>
<link rel="stylesheet" href="https://fonts.googleapis.com/css2?family=Ubuntu:wght@400;500;700&display=swap">
<style>
:root{
  --night:#16081c;
  --plum:#3a0f3f;
  --magenta:#b0246f;
  --pink:#ec4a8f;
  --pink-soft:#f06aa3;
  --blue:#2b8fe0;
  --blue-link:#2f8fd8;
  --ink:#333333;
  --muted:#666666;
  --line:#cfcfcf;
  --white:#ffffff;
  --panel:#f2f2f2;
  --photo:#9a6a55;
}
*{box-sizing:border-box;margin:0;padding:0}
html,body{width:1076px;height:1200px;overflow:hidden}
body{
  position:relative;font-family:"Ubuntu",Arial,sans-serif;color:var(--ink);
  background:
    radial-gradient(ellipse 60% 30% at 85% 25%,rgba(236,74,143,.45),transparent 70%),
    radial-gradient(ellipse 70% 25% at 20% 90%,rgba(176,36,111,.45),transparent 70%),
    linear-gradient(160deg,var(--plum) 0%,var(--night) 55%,#2a0a2c 100%);
}
.abs{position:absolute}

/* header */
.site-header{position:absolute;left:0;top:0;width:1076px;height:60px;background:rgba(18,6,22,.92);border-bottom:1px solid #3b2340}
.brand{position:absolute;left:26px;top:13px;font-size:31px;font-weight:400;color:var(--white);letter-spacing:-.3px;display:flex;align-items:center;gap:10px}
.brand-dot{width:14px;height:14px;border-radius:50%;background:var(--pink)}
.main-nav a{position:absolute;top:23px;font-size:14px;color:#b9b2bd;text-decoration:none}
.main-nav .support{color:var(--blue-link)}
.main-nav .account{color:var(--pink)}
.main-nav svg{position:absolute;top:22px}

/* content sheet */
.sheet{position:absolute;left:161px;top:88px;width:890px;height:997px;background:var(--white)}
.timeline{position:absolute;left:208px;top:88px;width:4px;height:997px;border-left:1px solid #dedede;border-right:1px solid #dedede}

/* profile card */
.profile-card{position:absolute;left:25px;top:98px;width:147px;height:844px;background:var(--white);box-shadow:0 0 4px rgba(0,0,0,.35)}
.profile-head{height:289px;background:var(--pink);position:relative}
.profile-photo{position:absolute;left:9px;top:10px;width:128px;height:144px;background:linear-gradient(160deg,#5a3a2e,#b48a6e 55%,#3d2620)}
.profile-name{position:absolute;left:9px;top:160px;font-size:16px;font-weight:700;color:var(--white)}
.profile-meta{position:absolute;left:9px;font-size:11.5px;color:var(--white);font-weight:500}
.card-btn{position:absolute;left:9px;width:128px;height:25px;background:#f4f4f4;border:1px solid #ddd;font-size:12px;color:#555;display:flex;align-items:center;gap:12px;padding-left:8px;letter-spacing:.5px}
.card-section{position:absolute;left:9px;width:130px}
.card-title{font-size:13px;color:var(--blue-link);font-weight:500;margin-bottom:7px}
.fact{font-size:11.8px;color:#444;height:23.7px}
.fact b{font-weight:700;color:#222}
.card-rule{position:absolute;left:9px;width:130px;border-top:1px solid #d8d8d8}
.swatch{position:absolute;width:40px;height:27px;border-radius:2px}

/* timeline hearts */
.heart{position:absolute;left:186px;width:48px;height:46px}

/* content boxes */
.post{position:absolute;left:252px;width:520px;background:var(--white);border:1px solid #cfcfcf}
.post::before{content:"";position:absolute;left:-9px;top:12px;width:16px;height:16px;background:var(--white);border-left:1px solid #cfcfcf;border-bottom:1px solid #cfcfcf;transform:rotate(45deg)}
.post-title{position:absolute;left:20px;top:18px;font-size:14.5px;color:var(--blue-link);font-weight:500}
.status-text{position:absolute;left:20px;top:49px;font-size:15px;color:#555}
.post-body{position:absolute;left:20px;top:47px;width:484px;font-size:11.9px;line-height:19.4px;color:#555}
.post-body p{margin-bottom:19.4px}
.post-body p.tight{margin-bottom:0}
.tag{color:var(--pink);font-weight:500}

/* right column */
.beta-banner{position:absolute;left:792px;top:88px;width:259px;height:62px;background:var(--blue);color:var(--white);font-size:16px;line-height:20px;padding:12px 16px}
.side-title{position:absolute;left:810px;width:222px;font-size:13px;color:var(--blue-link);padding-bottom:7px;border-bottom:1px solid #e6e6e6}
.search-box{position:absolute;left:812px;top:199px;width:219px;height:29px;border:2px solid #e2e2e2;font-size:14px;color:#555;padding:4px 9px}
.search-box svg{position:absolute;right:7px;top:5px}
.person{position:absolute;left:811px;width:220px;height:52px}
.avatar{position:absolute;width:50px;height:50px;background:linear-gradient(150deg,#4b2a1e,#a0735a 50%,#5a3526)}
.person-name{position:absolute;left:62px;top:0;font-size:13px;font-weight:700;color:#333}
.person-meta{position:absolute;left:62px;top:19px;font-size:12px;line-height:16px;color:#777}
.event{position:absolute;left:819px;width:210px;font-size:12px;line-height:14px;color:#555;padding-left:24px}
.event b{color:#222}
.event svg{position:absolute;left:0;top:0}
.match-grid{position:absolute;left:811px;top:753px;width:220px;height:177px;background:var(--panel)}
.match{position:absolute;width:50px;text-align:center}
.match .avatar{position:static;display:block}
.match span{display:block;font-size:11.5px;font-weight:700;color:#333;margin-top:4px}

.chat-btn{position:absolute;left:934px;top:1167px;width:117px;height:33px;background:var(--blue);border-radius:4px 4px 0 0;color:var(--white);font-size:11.5px;font-weight:700;display:flex;align-items:center;gap:8px;padding-left:10px}
</style>
</head>
<body>

<header class="site-header">
  <div class="brand"><span>WinkAtWheel</span><span class="brand-dot"></span></div>
  <nav class="main-nav">
    <a style="left:488px" href="#">Home</a>
    <a style="left:556px" href="#">Profile</a>
    <a style="left:628px" href="#">Message</a>
    <a style="left:715px" href="#">Matches</a>
    <a style="left:798px" href="#">Search</a>
    <svg style="left:869px" width="17" height="17" viewBox="0 0 17 17"><path d="M3 9a5.5 5.5 0 0 1 11 0" fill="none" stroke="#2f8fd8" stroke-width="2"/><rect x="2" y="9" width="3" height="5" rx="1" fill="#2f8fd8"/><rect x="12" y="9" width="3" height="5" rx="1" fill="#2f8fd8"/></svg>
    <a class="support" style="left:894px" href="#">Support</a>
    <svg style="left:958px" width="15" height="17" viewBox="0 0 15 17"><circle cx="7.5" cy="5" r="4" fill="#ec4a8f"/><path d="M0 17a7.5 6 0 0 1 15 0z" fill="#ec4a8f"/></svg>
    <a class="account" style="left:980px" href="#">My Account</a>
  </nav>
</header>

<main>
  <div class="sheet"></div>
  <div class="timeline"></div>

  <aside class="profile-card">
    <div class="profile-head">
      <div class="profile-photo" role="img" aria-label="Profile photo of Linda"></div>
      <div class="profile-name">Linda</div>
      <div class="profile-meta" style="top:184px">Age: 19 years old</div>
      <div class="profile-meta" style="top:202px">From: Wakefield</div>
      <div class="card-btn" style="top:215px">
        <svg width="13" height="11" viewBox="0 0 13 11"><rect x="0" y="2" width="13" height="9" rx="1.5" fill="#ec4a8f"/><rect x="4" y="0" width="5" height="3" fill="#ec4a8f"/><circle cx="6.5" cy="6.5" r="2.3" fill="#fff"/></svg>PROFILE</div>
      <div class="card-btn" style="top:244px">
        <svg width="11" height="12" viewBox="0 0 11 12"><path d="M5.5 0L11 6H7.5v6h-4V6H0z" fill="#ec4a8f"/></svg>GALLERY</div>
    </div>

    <section class="card-section" style="top:300px">
      <h3 class="card-title">About Me</h3>
      <div class="fact"><b>Eye:</b> Brown</div>
      <div class="fact"><b>Hair:</b> Black</div>
      <div class="fact"><b>Height:</b> 4’3”</div>
      <div class="fact"><b>Body:</b> Average</div>
      <div class="fact"><b>Education:</b> University</div>
      <div class="fact"><b>Children:</b> No children</div>
      <div class="fact"><b>Smoking:</b> Sometimes</div>
      <div class="fact"><b>Drinking:</b> Often</div>
    </section>
    <div class="card-rule" style="top:522px"></div>

    <section class="card-section" style="top:533px">
      <h3 class="card-title">My Car</h3>
      <div class="fact"><b>Make:</b> Vortexa</div>
      <div class="fact"><b>Model:</b> VX9</div>
      <div class="fact"><b>Colour:</b> Pink</div>
    </section>
    <div class="card-rule" style="top:635px"></div>

    <section class="card-section" style="top:646px">
      <h3 class="card-title">Select Background</h3>
    </section>
    <div class="swatch" style="left:9px;top:672px;background:#9fbf84" role="img" aria-label="Green background option"></div>
    <div class="swatch" style="left:55px;top:672px;background:#4c7a2a" role="img" aria-label="Leaves background option"></div>
    <div class="swatch" style="left:100px;top:672px;background:#8a4a22" role="img" aria-label="Warm lights background option"></div>
    <div class="swatch" style="left:9px;top:707px;background:#6f6a52" role="img" aria-label="Pebbles background option"></div>
    <div class="swatch" style="left:55px;top:707px;background:#8a4e28" role="img" aria-label="Wood background option"></div>
    <div class="swatch" style="left:100px;top:707px;background:#5c5c5c" role="img" aria-label="Stones background option"></div>
    <div class="swatch" style="left:9px;top:742px;background:#a38a66" role="img" aria-label="Sand background option"></div>
    <div class="swatch" style="left:55px;top:742px;background:#2e4a78" role="img" aria-label="Navy background option"></div>
    <div class="swatch" style="left:100px;top:742px;background:#6d706a" role="img" aria-label="Mountains background option"></div>
    <div class="swatch" style="left:9px;top:777px;background:#c8862e" role="img" aria-label="Golden field background option"></div>
    <div class="swatch" style="left:55px;top:777px;background:#4a4036" role="img" aria-label="Crowd background option"></div>
    <div class="swatch" style="left:100px;top:777px;background:#6a4a6a" role="img" aria-label="Dusk road background option"></div>
    <div class="swatch" style="left:9px;top:812px;background:#7cc0e0" role="img" aria-label="Sky blue background option"></div>
    <div class="swatch" style="left:55px;top:812px;background:#7a4a28" role="img" aria-label="Bokeh background option"></div>
    <div class="swatch" style="left:100px;top:812px;background:#3f7a22" role="img" aria-label="Green leaves background option"></div>
  </aside>

  <!-- timeline markers -->
  <svg class="heart" style="top:129px" viewBox="0 0 48 46"><path d="M24 45C8 33 0 25 0 14A12 12 0 0 1 24 8a12 12 0 0 1 24 6c0 11-8 19-24 31z" fill="#ec4a8f"/><path d="M15 13h18v11H22l-5 4v-4h-2z" fill="#fff"/></svg>
  <svg class="heart" style="top:243px" viewBox="0 0 48 46"><path d="M24 45C8 33 0 25 0 14A12 12 0 0 1 24 8a12 12 0 0 1 24 6c0 11-8 19-24 31z" fill="#ec4a8f"/><rect x="17" y="11" width="13" height="16" fill="#fff"/><path d="M20 16h7M20 19h7M20 22h7" stroke="#ec4a8f" stroke-width="1.4"/></svg>
  <svg class="heart" style="top:456px" viewBox="0 0 48 46"><path d="M24 45C8 33 0 25 0 14A12 12 0 0 1 24 8a12 12 0 0 1 24 6c0 11-8 19-24 31z" fill="#ec4a8f"/><circle cx="24" cy="19" r="8" fill="#fff"/><circle cx="21" cy="17" r="1.2" fill="#ec4a8f"/><circle cx="27" cy="17" r="1.2" fill="#ec4a8f"/><path d="M20 21a4 4 0 0 0 8 0" fill="none" stroke="#ec4a8f" stroke-width="1.5"/></svg>

  <article class="post" style="top:128px;height:83px">
    <h2 class="post-title">My Status</h2>
    <div class="status-text">“Lorem ipsum dolor”</div>
  </article>

  <article class="post" style="top:242px;height:182px">
    <h2 class="post-title">My Bio</h2>
    <div class="post-body">Lorem ipsum dolor sit amet, consectetur adipisicing elit, sed do eiusmod tempor incididunt ut labore et dolore magna aliqua. Ut enim ad minim veniam, quis nostrud exercitation ullamco laboris nisi ut aliquip ex ea commodo consequat. Duis aute irure dolor in reprehenderit in voluptate velit esse cillum dolore eu fugiat nulla pariatur. Excepteur sint occaecat cupidatat non proident, sunt in culpa qui officia deserunt mollit anim id est laborum.</div>
  </article>

  <article class="post" style="top:455px;height:558px">
    <h2 class="post-title">My Lifestyle</h2>
    <div class="post-body">
      <p><span class="tag">MOVIES:</span> Lorem Ipsum is simply dummy text of the printing and typesetting industry. Lorem Ipsum has been the industry's standard dummy text ever since the 1500s</p>
      <p><span class="tag">TV:</span> Lorem Ipsum is simply dummy text of the printing and typesetting industry. Lorem Ipsum has been the industry's standard dummy text ever since the 1500s, when an unknown printer took a galley of type and scrambled it to make a type specimen book. It has survived not only five centuries, but also the leap into electronic typesetting, remaining essentially unchanged. It was popularised in the 1960s with the release of Lettrex sheets containing Lorem Ipsum passages, and more recently with desktop publishing software like Alder PageSmith including versions of Lorem Ipsum.</p>
      <p><span class="tag">MUSIC:</span> Lorem Ipsum is simply dummy text of the printing and typesetting industry</p>
      <p class="tight"><span class="tag">PETS:</span> Lorem Ipsum is simply dummy text of the printing</p>
      <p><span class="tag">LANGUAGES:</span> Lorem Ipsum is simply dummy text</p>
      <p><span class="tag">INTERESTS:</span> Lorem Ipsum is simply dummy text of the printing and typesetting industry. Lorem Ipsum has been the industry's standard dummy text ever since the 1500s, when an unknown printer took a galley of type and scrambled it to make a type specimen book. It has survived not only five centuries, but also the leap into electronic typesetting, remaining essentially unchanged. It was popularised in the 1960s with the release of Lettrex sheets containing Lorem Ipsum passages, and more recently with desktop publishing software like Alder PageSmith including versions of Lorem Ipsum.</p>
    </div>
  </article>

  <aside>
    <div class="beta-banner">Welcome, Our site is currently free during beta testing.</div>

    <h3 class="side-title" style="top:165px">Your Favourites</h3>
    <div class="search-box">Type a name
      <svg width="16" height="16" viewBox="0 0 16 16"><circle cx="6.5" cy="6.5" r="5" fill="none" stroke="#ec4a8f" stroke-width="2"/><path d="M10 10l5 5" stroke="#ec4a8f" stroke-width="2.4"/></svg></div>

    <div class="person" style="top:241px"><div class="avatar" role="img" aria-label="Photo of jenny"></div><div class="person-name">jenny</div><div class="person-meta">19 years old<br>Leeds</div></div>
    <div class="person" style="top:306px"><div class="avatar" role="img" aria-label="Photo of jenny"></div><div class="person-name">jenny</div><div class="person-meta">19 years old<br>Leeds</div></div>
    <div class="person" style="top:370px"><div class="avatar" role="img" aria-label="Photo of jenny"></div><div class="person-name">jenny</div><div class="person-meta">19 years old<br>Leeds</div></div>
    <div class="person" style="top:435px"><div class="avatar" role="img" aria-label="Photo of jenny"></div><div class="person-name">jenny</div><div class="person-meta">19 years old<br>Leeds</div></div>
    <div class="person" style="top:499px"><div class="avatar" role="img" aria-label="Photo of jenny"></div><div class="person-name">jenny</div><div class="person-meta">19 years old<br>Leeds</div></div>

    <h3 class="side-title" style="top:577px">Your Matches</h3>
    <div class="event" style="top:613px"><svg width="14" height="12" viewBox="0 0 14 12"><rect y="2" width="14" height="10" rx="1.5" fill="#ec4a8f"/><rect x="4" width="6" height="3" fill="#ec4a8f"/><circle cx="7" cy="7" r="2.5" fill="#fff"/></svg><b>WAW</b> has uploaded a new image</div>
    <div class="event" style="top:655px"><svg width="14" height="12" viewBox="0 0 14 12"><rect y="2" width="14" height="10" rx="1.5" fill="#ec4a8f"/><rect x="4" width="6" height="3" fill="#ec4a8f"/><circle cx="7" cy="7" r="2.5" fill="#fff"/></svg><b>Lee</b> has uploaded a new image</div>
    <div class="event" style="top:696px"><svg width="14" height="14" viewBox="0 0 14 14"><path d="M7 1C3 1 0 3.5 0 6.5c0 2 1.2 3.6 3 4.5L2.5 14 6 12c.3 0 .7 0 1 0 4 0 7-2.5 7-5.5S11 1 7 1z" fill="#ec4a8f"/></svg><b>WAW</b> has updated his status</div>
    <div class="event" style="top:724px"><svg width="14" height="14" viewBox="0 0 14 14"><path d="M7 1C3 1 0 3.5 0 6.5c0 2 1.2 3.6 3 4.5L2.5 14 6 12c.3 0 .7 0 1 0 4 0 7-2.5 7-5.5S11 1 7 1z" fill="#ec4a8f"/></svg><b>Lee</b> has updated his status</div>

    <div class="match-grid">
      <div class="match" style="left:16px;top:16px"><div class="avatar" role="img" aria-label="Photo of jenny"></div><span>jenny</span></div>
      <div class="match" style="left:85px;top:16px"><div class="avatar" role="img" aria-label="Photo of jenny"></div><span>jenny</span></div>
      <div class="match" style="left:154px;top:16px"><div class="avatar" role="img" aria-label="Photo of jenny"></div><span>jenny</span></div>
      <div class="match" style="left:16px;top:94px"><div class="avatar" role="img" aria-label="Photo of jenny"></div><span>jenny</span></div>
      <div class="match" style="left:85px;top:94px"><div class="avatar" role="img" aria-label="Photo of jenny"></div><span>jenny</span></div>
      <div class="match" style="left:154px;top:94px"><div class="avatar" role="img" aria-label="Photo of jenny"></div><span>jenny</span></div>
    </div>
  </aside>
</main>

<div class="chat-btn">
  <svg width="18" height="16" viewBox="0 0 18 16"><path d="M6 1C2.7 1 0 3 0 5.5c0 1.5.9 2.7 2.3 3.5L2 12l3-2c.3 0 .7 0 1 0 3.3 0 6-2 6-4.5S9.3 1 6 1z" fill="#fff"/><path d="M13 6c2.8.3 5 2.1 5 4.3 0 1.3-.8 2.4-2 3.1l.3 2.6-2.7-1.8c-2.6 0-4.8-1.2-5.5-2.9 2.7-.4 4.7-2.4 4.9-5.3z" fill="#fff"/></svg>
  OPEN CHAT
</div>

</body>
</html>
```